Melorix artwork for new single release

I need Melorix artwork creating to release a new single on there.

The specs are:

Ideal size: 3000 x 3000 pixels
Minimum size: 1400 x 1400 pixels
Aspect ratio: 1:1 (must be a perfect square)
File format: JPG or PNG
Color space: sRGB
File size: Max 4MB

The song is called "Was It Ever Rain?"
The artist is "Martin Hollow"

We have no images of Martin, so it really is open to imagination.

Target Market(s)

Melorix listeners

Industry/Entity Type

Music

```html
<!DOCTYPE html>
<html lang="en">
<head>
<meta charset="utf-8">
<title>Was It Ever Rain? — Martin Hollow</title>
<link rel="stylesheet" href="https://fonts.googleapis.com/css2?family=Italiana&display=swap">
<style>
  :root {
    --sky: #6f9fbf;
    --steel: #4d6a93;
    --dusk: #8a7196;
    --rose: #c98479;
    --plum: #8a5872;
    --ink-light: #e6ecfb;
    --title: #fbf6f0;
    --glow: rgba(255, 196, 110, 0.85);
    --art-blue: #7ec4e8;
    --art-pink: #f0a895;
  }
  * { margin: 0; padding: 0; box-sizing: border-box; }
  html, body { width: 1200px; height: 1200px; overflow: hidden; }
  body { background: var(--steel); }
  .cover {
    position: relative;
    width: 1200px;
    height: 1200px;
    overflow: hidden;
    background:
      linear-gradient(180deg, rgba(255,255,255,0) 55%, rgba(60,50,100,0.35) 100%),
      linear-gradient(90deg, var(--sky) 0%, var(--steel) 30%, var(--dusk) 52%, var(--rose) 78%, var(--plum) 100%);
    font-family: "Italiana", serif;
  }
  .artwork {
    position: absolute;
    left: 60px;
    top: 250px;
    width: 1080px;
    height: 680px;
    border-radius: 50%;
    background:
      radial-gradient(ellipse 30% 45% at 50% 48%, rgba(255,235,240,0.85), rgba(255,235,240,0) 70%),
      radial-gradient(ellipse 35% 55% at 33% 50%, var(--art-blue), rgba(126,196,232,0) 75%),
      radial-gradient(ellipse 35% 55% at 68% 50%, var(--art-pink), rgba(240,168,149,0) 75%),
      radial-gradient(ellipse 50% 50% at 50% 55%, rgba(70,60,110,0.55), rgba(70,60,110,0) 80%);
    filter: blur(6px);
  }
  .player { position: absolute; left: 0; top: 0; width: 1200px; height: 360px; }
  .title {
    position: absolute;
    left: 0; right: 0;
    top: 772px;
    text-align: center;
    font-size: 138px;
    font-weight: 400;
    line-height: 1;
    color: var(--title);
    letter-spacing: -1px;
    text-shadow: 0 0 14px var(--glow), 0 0 30px rgba(255, 170, 90, 0.55);
    white-space: nowrap;
  }
  .artist {
    position: absolute;
    left: 0; right: 0;
    top: 945px;
    text-align: center;
    font-size: 86px;
    line-height: 1;
    color: var(--title);
    white-space: nowrap;
  }
  .rule {
    position: absolute;
    left: 365px;
    top: 1060px;
    width: 470px;
    height: 1.5px;
    background: var(--ink-light);
  }
</style>
</head>
<body>
  <main class="cover">
    <div class="artwork" role="img" aria-label="Cover artwork area in soft blue and rose tones"></div>

    <svg class="player" viewBox="0 0 1200 360" aria-hidden="true">
      <g class="progress" fill="var(--ink-light)" stroke="var(--ink-light)">
        <line x1="323" y1="94" x2="877" y2="94" stroke-width="6" stroke-linecap="round"/>
        <circle cx="438" cy="94" r="10" stroke="none"/>
      </g>

      <g class="controls" fill="none" stroke="var(--ink-light)" stroke-width="4" stroke-linecap="round" stroke-linejoin="round">
        <g class="shuffle">
          <path d="M334 172 H344 C356 172 360 192 372 192 H378"/>
          <path d="M334 192 H344 C356 192 360 172 372 172 H378"/>
          <path d="M372 166 L379 172 L372 178 M372 186 L379 192 L372 198"/>
        </g>
        <g class="previous" fill="var(--ink-light)" stroke="none">
          <path d="M462 170 L443 182 L462 194 Z"/>
          <path d="M482 170 L463 182 L482 194 Z"/>
        </g>
        <circle class="play" cx="599" cy="182" r="27" fill="var(--ink-light)" stroke="none"/>
        <path d="M591 168 L612 182 L591 196 Z" fill="#7a86ad" stroke="none"/>
        <g class="next" fill="var(--ink-light)" stroke="none">
          <path d="M717 170 L736 182 L717 194 Z"/>
          <path d="M737 170 L756 182 L737 194 Z"/>
        </g>
        <g class="repeat">
          <path d="M846 170 H872 V192"/>
          <path d="M868 194 H842 V172"/>
          <path d="M852 164 L846 170 L852 176 M862 188 L868 194 L862 200"/>
        </g>
      </g>

      <g class="waveform" stroke="var(--ink-light)" stroke-width="7" stroke-linecap="round">
        <line x1="333" y1="288" x2="333" y2="320"/>
        <line x1="352" y1="278" x2="352" y2="330"/>
        <line x1="370" y1="266" x2="370" y2="344"/>
        <line x1="389" y1="282" x2="389" y2="326"/>
        <line x1="407" y1="288" x2="407" y2="320"/>
        <line x1="425" y1="272" x2="425" y2="336"/>
        <line x1="444" y1="284" x2="444" y2="324"/>
        <line x1="462" y1="264" x2="462" y2="346"/>
        <line x1="481" y1="278" x2="481" y2="330"/>
        <line x1="499" y1="268" x2="499" y2="340"/>
        <line x1="517" y1="286" x2="517" y2="322"/>
        <line x1="536" y1="276" x2="536" y2="332"/>
        <line x1="554" y1="290" x2="554" y2="318"/>
        <line x1="573" y1="270" x2="573" y2="338"/>
        <line x1="591" y1="282" x2="591" y2="326"/>
        <line x1="609" y1="266" x2="609" y2="342"/>
        <line x1="628" y1="286" x2="628" y2="322"/>
        <line x1="646" y1="272" x2="646" y2="336"/>
        <line x1="665" y1="280" x2="665" y2="328"/>
        <line x1="683" y1="264" x2="683" y2="344"/>
        <line x1="701" y1="288" x2="701" y2="320"/>
        <line x1="720" y1="276" x2="720" y2="332"/>
        <line x1="738" y1="268" x2="738" y2="340"/>
        <line x1="757" y1="284" x2="757" y2="324"/>
        <line x1="775" y1="262" x2="775" y2="346"/>
        <line x1="793" y1="278" x2="793" y2="330"/>
        <line x1="812" y1="288" x2="812" y2="320"/>
        <line x1="830" y1="270" x2="830" y2="338"/>
        <line x1="849" y1="264" x2="849" y2="344"/>
        <line x1="867" y1="282" x2="867" y2="326"/>
      </g>
    </svg>

    <h1 class="title">Was It Ever Rain?</h1>
    <p class="artist">Martin Hollow</p>
    <div class="rule"></div>
  </main>
</body>
</html>
```